KLW AUDITION

I need a post card design (front only) with this on it:
Bold Rising Steps (this is the main title to be in all caps)
Auditions
Date: Thursday June 30th
6:30-8:30 PM in person
Address: 4172 Fernwick BLVD, Oakland CA 94603
video submissions turn in by Sunday July 3rd, 2022 email:BoldRisingSteps22@tolvamail.com
Teens and Adults welcomed

SO PLEASE COME UP WITH A DESIGN THATS COLORFUL AND INVITING THX!

```html
<!DOCTYPE html>
<html lang="en">
<head>
<meta charset="utf-8">
<title>Bold Rising Steps – Auditions</title>
<link rel="stylesheet" href="https://fonts.googleapis.com/css2?family=Archivo+Black&family=Great+Vibes&family=Montserrat:wght@300;400;600;700&display=swap">
<style>
  :root{
    --night:#000000;
    --maroon:#3a0714;
    --wine:#5c0a2a;
    --magenta:#c2186b;
    --ember:#ff6a00;
    --lime:#39ff14;
    --leaf:#2f7d18;
    --mint:#e9ffe0;
    --sun:#ffef1a;
    --white:#ffffff;
  }
  *{margin:0;padding:0;box-sizing:border-box}
  html,body{width:1200px;height:1200px;overflow:hidden;background:var(--night)}
  .postcard{position:relative;width:1200px;height:1200px;background:var(--night);overflow:hidden;font-family:"Montserrat",sans-serif;color:var(--white)}
  .stage-backdrop{position:absolute;left:0;top:0;width:1200px;height:830px;
    background:
      radial-gradient(ellipse 300px 160px at 620px 700px, rgba(255,106,0,.85), transparent 70%),
      radial-gradient(ellipse 380px 220px at 700px 470px, rgba(194,24,107,.75), transparent 70%),
      radial-gradient(ellipse 260px 200px at 1150px 420px, rgba(180,190,20,.55), transparent 70%),
      radial-gradient(ellipse 260px 260px at 60px 380px, rgba(220,60,20,.5), transparent 70%),
      linear-gradient(180deg, var(--maroon) 0%, var(--wine) 45%, #4a1230 80%, var(--night) 100%);}
  .dancer-photo{position:absolute;left:130px;top:80px;width:420px;height:690px;border-radius:200px 200px 120px 120px;
    background:linear-gradient(170deg, rgba(190,190,190,.55) 0%, rgba(200,170,150,.5) 40%, rgba(80,190,230,.6) 70%, rgba(220,40,110,.55) 100%);}
  .title{position:absolute;left:0;top:0;width:1200px;height:600px}
  .title text{font-family:"Archivo Black",sans-serif;font-size:168px}
  .script{position:absolute;left:497px;top:585px;font-family:"Great Vibes",cursive;font-size:190px;color:var(--white);line-height:1;text-shadow:0 3px 8px rgba(0,0,0,.35)}
  .schedule{position:absolute;left:99px;top:864px}
  .schedule-row{display:flex;align-items:center;gap:22px;height:58px;font-size:38px;font-weight:600}
  .schedule-row svg{width:44px;height:44px}
  .divider{position:absolute;left:586px;top:854px;height:142px;border-left:2px dotted #bbbbbb}
  .deadline{position:absolute;left:645px;top:866px;width:480px;height:130px;border:2px solid var(--lime);border-radius:0 32px 32px 0;border-left:none}
  .deadline-bell{position:absolute;left:607px;top:893px;width:75px;height:75px;border-radius:50%;border:2px solid var(--lime);background:var(--night);display:flex;align-items:center;justify-content:center}
  .deadline-text{position:absolute;left:702px;top:878px;color:var(--sun);line-height:1.15}
  .deadline-text .lead{font-size:27px;font-weight:400}
  .deadline-text .date{font-size:34px;font-weight:700}
  .deadline-text .email{margin-top:4px;font-size:18px;font-weight:600;color:var(--white)}
  .address-band{position:absolute;left:0;top:1041px;width:819px;height:47px;background:var(--lime)}
  .address-pin{position:absolute;left:93px;top:1031px;width:58px;height:58px;border-radius:50%;background:var(--lime);display:flex;align-items:center;justify-content:center}
  .address-text{position:absolute;left:164px;top:1044px;font-size:31px;font-weight:700;color:var(--night);line-height:40px}
  .welcome-rule{position:absolute;left:96px;top:1148px;width:454px;border-top:2px dotted var(--lime)}
  .welcome-icon{position:absolute;left:563px;top:1128px;width:52px;height:46px}
  .welcome-text{position:absolute;left:628px;top:1129px;font-size:31px;font-weight:400;letter-spacing:.5px}
</style>
</head>
<body>
<main class="postcard">
  <div class="stage-backdrop" role="img" aria-label="Colourful stage lights with bokeh circles, music notes and a cheering crowd in silhouette"></div>
  <div class="dancer-photo" role="img" aria-label="Photo of a dancer leaping mid-air in a grey crop top, blue pants and pink sneakers"></div>

  <svg class="title" viewBox="0 0 1200 600" aria-label="BOLD RISING STEPS">
    <defs>
      <linearGradient id="titleFill" x1="0" y1="0" x2="0" y2="1">
        <stop offset="0" stop-color="#ffffff"/>
        <stop offset="0.5" stop-color="#d8f7c8"/>
        <stop offset="1" stop-color="#8ee86a"/>
      </linearGradient>
    </defs>
    <g fill="url(#titleFill)" stroke="var(--leaf)" stroke-width="5" paint-order="stroke" transform="skewX(-6)">
      <text x="425" y="282" textLength="600" lengthAdjust="spacingAndGlyphs">BOLD</text>
      <text x="285" y="421" textLength="838" lengthAdjust="spacingAndGlyphs">RISING</text>
      <text x="318" y="560" textLength="818" lengthAdjust="spacingAndGlyphs">STEPS</text>
    </g>
  </svg>

  <div class="script">Auditions</div>

  <section class="schedule">
    <div class="schedule-row">
      <svg viewBox="0 0 44 44" fill="none" stroke="#39ff14" stroke-width="3"><rect x="4" y="7" width="36" height="33" rx="3"/><line x1="4" y1="16" x2="40" y2="16"/><line x1="13" y1="3" x2="13" y2="10"/><line x1="31" y1="3" x2="31" y2="10"/><g fill="#39ff14" stroke="none"><rect x="10" y="21" width="5" height="5"/><rect x="19" y="21" width="5" height="5"/><rect x="28" y="21" width="5" height="5"/><rect x="10" y="30" width="5" height="5"/><rect x="19" y="30" width="5" height="5"/><rect x="28" y="30" width="5" height="5"/></g></svg>
      <span>30th June,Thursday</span>
    </div>
    <div class="schedule-row">
      <svg viewBox="0 0 44 44" fill="none" stroke="#39ff14" stroke-width="3" stroke-linecap="round"><path d="M30 7 A18 18 0 1 0 22 40"/><polyline points="20,12 20,23 27,27"/><circle cx="34" cy="34" r="8"/><polyline points="30,34 33,37 38,31"/></svg>
      <span>6:30 - 8:30 PM</span>
    </div>
  </section>

  <div class="divider"></div>

  <div class="deadline"></div>
  <div class="deadline-bell">
    <svg width="46" height="40" viewBox="0 0 46 40" fill="none" stroke="#fff" stroke-width="2.5" stroke-linecap="round"><path d="M15 29 V19 a8 8 0 0 1 16 0 V29 Z" fill="#fff"/><line x1="12" y1="30" x2="34" y2="30"/><circle cx="23" cy="34" r="2.5" fill="#fff"/><path d="M9 12 Q5 19 9 26"/><path d="M5 9 Q0 19 5 29"/><path d="M37 12 Q41 19 37 26"/><path d="M41 9 Q46 19 41 29"/></svg>
  </div>
  <div class="deadline-text">
    <div class="lead">video submissions turn in by</div>
    <div class="date">Sunday July 3rd, 2022</div>
    <div class="email">email: BoldRisingSteps22@tolvamail.com</div>
  </div>

  <div class="address-band"></div>
  <div class="address-pin">
    <svg width="36" height="42" viewBox="0 0 36 42" fill="none" stroke="#000" stroke-width="3"><path d="M18 30 C10 20 8 16 8 12 a10 10 0 0 1 20 0 c0 4 -2 8 -10 18 Z"/><circle cx="18" cy="12" r="3.5"/><ellipse cx="18" cy="34" rx="14" ry="5"/></svg>
  </div>
  <div class="address-text">4172 Fernwick BLVD, Oakland CA 94603</div>

  <div class="welcome-rule"></div>
  <svg class="welcome-icon" viewBox="0 0 52 46" fill="none" stroke="#39ff14" stroke-width="3" stroke-linecap="round" stroke-linejoin="round"><path d="M18 40 L12 24 a3 3 0 0 1 5 -2 l4 6 L17 12 a3 3 0 0 1 6 -1 l4 12 l-1 -15 a3 3 0 0 1 6 0 l2 16 l3 -7 a3 3 0 0 1 5 2 l-4 16 Q36 44 26 44 Z"/><path d="M4 10 Q6 4 12 3"/><path d="M3 17 Q2 10 6 6"/></svg>
  <div class="welcome-text">TEENS AND ADULTS WELCOMED</div>
</main>
</body>
</html>
```